Marlow Dermal Studio - Business Banner with Brand Elements

Design:
• We would like to get a creative design for a wide banner that will go outside our medical spa clinic location. We need a designer to make a simple yet colorful and high-quality design layout. We want this banner to be eye-catching and to communicate the services we offer at our business: Laser Hair Removal | Veluxin | Lip Filler.

Requirements:
• We would like the banner to include our companies information which is the following:

Logo
“Refresh Your Skin”
Laser Hair Removal | Veluxin | Lip Filler
(520) 867-2291
www.MarlowDermalStudio.com

Colors:
• Our business colors are orange, a hint of black and white, but mostly peach/orange tones. (Orange: #f78f20 , White: #ffffff)

Fonts:
• Josefins Sans Bold & Lato

Content and images can be located here:
https://files.quibbleshare.com/share/folders/7tKwP3zRa9_LmQxVb2nD5yHc04EeJuFs8?mode=viewing

The following will give you an idea of our brand presentation:
• Our website is: www.MarlowDermalStudio.com
• Our Pictavo; @marlowdermalstudio
• Our Lumora: www.lumoranet.com/marlowdermalstudio

Target Market(s)
• Women 25 - 45

Industry/Entity Type
• Beauty

```html
<!DOCTYPE html>
<html lang="en">
<head>
<meta charset="utf-8">
<title>Marlow Dermal Studio – Outdoor Banner</title>
<link rel="stylesheet" href="https://fonts.googleapis.com/css2?family=Josefin+Sans:wght@300;600;700&family=Lato:wght@400;700&display=swap">
<style>
  :root {
    --orange: #f78f20;
    --charcoal: #3f3f41;
    --ink: #2b2b2d;
    --white: #ffffff;
    --stage: #7a7a7a;
  }
  html, body {
    margin: 0;
    padding: 0;
    width: 1200px;
    height: 818px;
    overflow: hidden;
    background: var(--stage);
  }
  .banner {
    position: absolute;
    left: 40px;
    top: 200px;
    width: 1120px;
    height: 419px;
    background: var(--orange);
    overflow: hidden;
    font-family: "Josefin Sans", "Lato", sans-serif;
  }
  .banner-shapes, .banner-photo {
    position: absolute;
    left: 0;
    top: 0;
    width: 1120px;
    height: 419px;
  }
  .headline-top {
    position: absolute;
    left: 80px;
    top: 40px;
    margin: 0;
    font-weight: 300;
    font-size: 100px;
    letter-spacing: 3px;
    line-height: 1;
    color: var(--charcoal);
  }
  .headline-bottom {
    position: absolute;
    left: 83px;
    top: 145px;
    margin: 0;
    font-weight: 700;
    font-size: 59px;
    letter-spacing: 15.5px;
    line-height: 1;
    color: var(--orange);
  }
  .service-list {
    position: absolute;
    left: 65px;
    top: 231px;
    width: 325px;
    display: flex;
    flex-direction: column;
    gap: 20px;
  }
  .service-row {
    display: flex;
    justify-content: space-between;
    gap: 8px;
  }
  .service {
    height: 38px;
    display: flex;
    align-items: center;
    gap: 9px;
    padding: 0 14px 0 4px;
    box-sizing: border-box;
    background: var(--ink);
    border-radius: 19px;
    color: var(--white);
    font-weight: 600;
    font-size: 21px;
    letter-spacing: 0.5px;
    white-space: nowrap;
  }
  .service-wide { width: 100%; gap: 16px; }
  .service-dot {
    width: 30px;
    height: 30px;
    border-radius: 50%;
    background: var(--orange);
    border: 2px solid var(--white);
    box-sizing: border-box;
    flex: none;
  }
  .service-text { padding-top: 4px; }
  .brand {
    position: absolute;
    left: 430px;
    top: 212px;
    width: 150px;
    display: flex;
    flex-direction: column;
    align-items: center;
    gap: 10px;
  }
  .brand-mark {
    width: 54px;
    height: 54px;
    border-radius: 50%;
    background: var(--orange);
  }
  .brand-name {
    margin: 0;
    text-align: center;
    font-weight: 700;
    font-size: 23px;
    line-height: 1.05;
    color: var(--ink);
  }
  .contact {
    position: absolute;
    left: 70px;
    top: 360px;
    display: flex;
    align-items: center;
    gap: 9px;
    font-weight: 700;
    font-size: 21px;
    color: var(--ink);
    white-space: nowrap;
  }
  .contact-icon { width: 22px; height: 22px; flex: none; }
  .contact-text { padding-top: 4px; }
  .contact-divider {
    width: 2px;
    height: 22px;
    background: var(--ink);
    margin: 0 6px;
  }
</style>
</head>
<body>
  <section class="banner" aria-label="Marlow Dermal Studio outdoor banner">
    <svg class="banner-shapes" viewBox="0 0 1120 419" aria-hidden="true">
      <path d="M49 0 Q-20 220 76 419 L651 419 Q580 220 673 0 Z" fill="#ffffff"/>
      <path d="M673 0 Q580 220 651 419 L1120 419 L1120 0 Z" fill="var(--charcoal)"/>
      <path d="M683 0 Q615 230 712 419 L1120 419 L1120 0 Z" fill="var(--orange)"/>
    </svg>

    <svg class="banner-photo" viewBox="0 0 1120 419" role="img" aria-label="Photo of a smiling young woman in an orange off-shoulder top with sunglasses on her head, on a sunny city waterfront">
      <defs>
        <linearGradient id="photoTone" x1="0" y1="0" x2="1" y2="1">
          <stop offset="0" stop-color="#8f9a8a"/>
          <stop offset="0.45" stop-color="#b89a7e"/>
          <stop offset="0.75" stop-color="#d9a24a"/>
          <stop offset="1" stop-color="#e8a93a"/>
        </linearGradient>
      </defs>
      <path d="M691 0 Q640 230 791 419 L1120 419 L1120 0 Z" fill="url(#photoTone)"/>
    </svg>

    <h1 class="headline-top">REFRESH</h1>
    <h2 class="headline-bottom">YOUR SKIN</h2>

    <div class="service-list">
      <div class="service service-wide"><span class="service-dot"></span><span class="service-text">LASER HAIR REMOVAL</span></div>
      <div class="service-row">
        <div class="service"><span class="service-dot"></span><span class="service-text">VELUXIN</span></div>
        <div class="service"><span class="service-dot"></span><span class="service-text">LIP FILLER</span></div>
      </div>
    </div>

    <div class="brand">
      <span class="brand-mark"></span>
      <p class="brand-name">Marlow<br>Dermal Studio</p>
    </div>

    <div class="contact">
      <svg class="contact-icon" viewBox="0 0 24 24" aria-hidden="true">
        <path d="M6.6 2.5l3 3.4-1.8 2.4c1.2 2.6 3.3 4.7 5.9 5.9l2.4-1.8 3.4 3-1.6 3.3c-.4.8-1.3 1.2-2.2 1C9.6 18.4 5.6 14.4 4.3 8.3c-.2-.9.2-1.8 1-2.2z" fill="none" stroke="var(--orange)" stroke-width="1.6" stroke-linejoin="round"/>
        <path d="M14 3.5a6.5 6.5 0 0 1 6.5 6.5M14 6.8a3.2 3.2 0 0 1 3.2 3.2" fill="none" stroke="var(--orange)" stroke-width="1.6" stroke-linecap="round"/>
      </svg>
      <span class="contact-text">(520) 867-2291</span>
      <span class="contact-divider"></span>
      <svg class="contact-icon" viewBox="0 0 24 24" aria-hidden="true">
        <circle cx="12" cy="12" r="9.5" fill="none" stroke="var(--orange)" stroke-width="1.6"/>
        <ellipse cx="12" cy="12" rx="4" ry="9.5" fill="none" stroke="var(--orange)" stroke-width="1.6"/>
        <path d="M2.5 12h19" stroke="var(--orange)" stroke-width="1.6"/>
      </svg>
      <span class="contact-text">www.MarlowDermalStudio.com</span>
    </div>
  </section>
</body>
</html>
```